Book cover design for a collection of poetry - The Lanternfield

Book cover and back design need to be moody, nostalgic, reflective, ethereal. Melancholy and other worldly. Cover design should not be time specific to a period or place but if applicable should reflect British landscape. Book cover should be in tones of blue and must include the title and author (THE LANTERNFIELD BY CORBIN WHITLACE). We love the idea of rain, and looking out of a window. See attached designs. A world you are observing but not in.

Industry/Entity Type

Book Publisher

Font styles to use
Serif
Script

Colors
3176b5
3377b5
85acd3
eaf1f7
0792cd
33a6d7
86cae7
ecf7fb
86cfc6

Requirements
Must have
• The colour blue in it, must be melancholy and reflective.
Nice to have
• Rain in the cover.
Should not have
• Any bright colours.

```html
<!DOCTYPE html>
<html lang="en">
<head>
<meta charset="utf-8">
<title>The Lanternfield — Corbin Whitlace</title>
<link rel="stylesheet" href="https://fonts.googleapis.com/css2?family=Italiana&family=Cormorant+Garamond:wght@500&display=swap">
<style>
  :root {
    --sky-top: #1fb0e6;
    --sky-upper: #1593d8;
    --sky-mid: #1d62c6;
    --dusk: #2e3598;
    --night: #28226a;
    --night-deep: #221c5e;
    --frame: #1a3454;
    --pane-glow: #eef6fc;
    --pane-light: #9fcdf0;
    --pane-mid: #4f95d6;
    --pane-deep: #4a5fae;
    --pane-violet: #6a73b8;
    --ink-light: #eef2fa;
  }
  * { margin: 0; padding: 0; box-sizing: border-box; }
  html, body { width: 754px; height: 1200px; overflow: hidden; background: var(--night); }
  .cover {
    position: relative;
    width: 754px;
    height: 1200px;
    overflow: hidden;
  }
  .cover__backdrop {
    position: absolute;
    inset: 0;
    background:
      radial-gradient(ellipse 60% 30% at 50% 8%, rgba(160, 225, 250, 0.35) 0%, rgba(160, 225, 250, 0) 100%),
      radial-gradient(ellipse 70% 25% at 50% 72%, rgba(70, 60, 160, 0.45) 0%, rgba(70, 60, 160, 0) 100%),
      linear-gradient(90deg, rgba(10, 30, 80, 0.25) 0%, rgba(10, 30, 80, 0) 18%, rgba(10, 30, 80, 0) 82%, rgba(10, 30, 80, 0.25) 100%),
      linear-gradient(180deg, var(--sky-top) 0%, var(--sky-upper) 22%, var(--sky-mid) 48%, var(--dusk) 64%, var(--night) 78%, var(--night-deep) 100%);
  }
  .cover__window {
    position: absolute;
    left: 130px;
    top: 193px;
    width: 507px;
    height: 502px;
  }
  .cover__window-view {
    position: absolute;
    inset: 0;
    background:
      radial-gradient(ellipse 34% 30% at 54% 30%, var(--pane-glow) 0%, rgba(200, 230, 250, 0.75) 35%, rgba(159, 205, 240, 0) 100%),
      radial-gradient(ellipse 40% 30% at 20% 20%, rgba(120, 190, 240, 0.6) 0%, rgba(120, 190, 240, 0) 100%),
      linear-gradient(180deg, var(--pane-mid) 0%, #5d9bd8 40%, var(--pane-deep) 65%, var(--pane-violet) 100%);
  }
  .cover__frames {
    position: absolute;
    inset: 0;
  }
  .cover__title {
    position: absolute;
    left: 0;
    top: 880px;
    width: 754px;
    height: 220px;
  }
  .title-main {
    font-family: "Italiana", "Cormorant Garamond", serif;
    fill: var(--ink-light);
  }
  .title-article {
    font-family: "Cormorant Garamond", serif;
    font-weight: 500;
    fill: var(--ink-light);
  }
  .title-author {
    font-family: "Cormorant Garamond", serif;
    font-weight: 500;
    fill: var(--ink-light);
  }
</style>
</head>
<body>
  <main class="cover">
    <div class="cover__backdrop" role="img" aria-label="Misty blue forest seen through a window pane covered in raindrops"></div>

    <div class="cover__window">
      <div class="cover__window-view" role="img" aria-label="Old frosted four-pane window looking out onto bare winter trees and pale light"></div>
      <svg class="cover__frames" width="507" height="502" viewBox="0 0 507 502" aria-hidden="true">
        <g fill="none" stroke="var(--frame)" stroke-opacity="0.88">
          <rect x="13" y="13" width="481" height="476" stroke-width="26"/>
          <line x1="257" y1="26" x2="257" y2="476" stroke-width="10"/>
          <line x1="26" y1="249" x2="481" y2="249" stroke-width="10"/>
          <rect x="120" y="109" width="273" height="271" stroke-width="14"/>
        </g>
        <rect x="26" y="26" width="455" height="450" fill="none" stroke="#0e2440" stroke-opacity="0.35" stroke-width="3"/>
      </svg>
    </div>

    <svg class="cover__title" width="754" height="220" viewBox="0 0 754 220">
      <text class="title-article" x="119" y="50" font-size="20" letter-spacing="2">THE</text>
      <text class="title-main" x="117" y="118" font-size="74" textLength="523" lengthAdjust="spacingAndGlyphs">LANTERNFIELD</text>
      <text class="title-author" x="169" y="175" font-size="25" textLength="420" lengthAdjust="spacing">BY CORBIN WHITLACE</text>
    </svg>
  </main>
</body>
</html>
```